Accountability Project Graphics

I want to create 10 social media graphics (new Instagram size 4:5 (1080 x 1350 pixels) focusing on our Quilvo Accountability App, using any of the 3 pictures attached. Use the attached pics only, NO RANDOM STOCK PHOTOGRAPHY. For the color scheme, use the landing page colors/fonts (attached).
You can add any of the 3 photos attached but I mainly need BOLD text that includes these headlines and sub-headlines on them.
Please NOTE for all the headlines below, also add this sub-headline on each graphic:
Stay Consistent with RT in Your Pocket!
Here are the headlines:
• Stop Starting Over Every Monday
• You don't need more willpower. You need more support
• Built for women who are tired of doing this alone
• When Motivation Fades, RT Checks In
• The Support System You've Been Missing
• Support When Motivation Disappears
• What if RT Checked in Every Day?
• The Missing Piece Isn't Another Diet
• Eat the food you love. Stay accountable every day.
• One Bad Meal Doesn't Mean You Failed
women over 40 trying to lose weight

```html
<!DOCTYPE html>
<html lang="en">
<head>
<meta charset="utf-8">
<title>Quilvo – Eat the food you love</title>
<link href="https://fonts.googleapis.com/css2?family=Playfair+Display:wght@400;700;800&family=Allura&family=Caveat:wght@500&family=Montserrat:wght@500;600;700&display=swap" rel="stylesheet">
<style>
  :root {
    --cream: #f6eee6;
    --plum: #3a1f4a;
    --ink: #23142f;
    --pink: #e8508a;
    --pink-soft: #f3c9dc;
    --note: #ecd3e6;
    --tape: #d9c2a6;
    --white: #ffffff;
    --photo-top: #f1dcd6;
    --photo-mid: #e6bfcb;
    --photo-low: #e4e6c4;
  }
  * { margin: 0; padding: 0; box-sizing: border-box; }
  html, body { width: 960px; height: 1200px; overflow: hidden; background: var(--cream); }
  .poster { position: relative; width: 960px; height: 1200px; overflow: hidden; background: var(--cream); font-family: 'Playfair Display', Georgia, serif; color: var(--ink); }

  .photo { position: absolute; left: 400px; top: 30px; width: 560px; height: 1040px;
    background: linear-gradient(180deg, var(--photo-top) 0%, var(--photo-mid) 45%, var(--photo-low) 100%);
    clip-path: polygon(12% 6%, 30% 3%, 48% 7%, 70% 2%, 100% 4%, 100% 100%, 20% 100%, 17% 88%, 13% 72%, 14% 55%, 11% 40%, 13% 22%); }

  .logo { position: absolute; left: 20px; top: 46px; width: 270px; height: 96px; }
  .logo svg { position: absolute; inset: 0; }
  .logo-name { position: absolute; left: 34px; top: 14px; font-family: 'Montserrat', sans-serif; font-weight: 600; font-size: 38px; letter-spacing: 3px; color: var(--white); }
  .logo-tag { position: absolute; left: 36px; top: 64px; font-family: 'Montserrat', sans-serif; font-weight: 500; font-size: 12.5px; letter-spacing: 3px; color: var(--pink); }

  .heart-top { position: absolute; left: 356px; top: 142px; }

  .headline { position: absolute; left: 50px; top: 190px; font-weight: 800; font-size: 78px; line-height: 70px; letter-spacing: -1px; }
  .headline .pink { color: var(--pink); }
  .rule-1 { position: absolute; left: 96px; top: 416px; }
  .subhead { position: absolute; left: 50px; top: 458px; font-weight: 800; font-size: 64px; line-height: 60px; letter-spacing: -1px; }
  .script { position: absolute; left: 46px; top: 574px; font-family: 'Allura', cursive; font-size: 104px; color: var(--pink); line-height: 1; }
  .rule-2 { position: absolute; left: 44px; top: 656px; }

  .promise { position: absolute; left: 28px; top: 700px; width: 390px; height: 134px; }
  .promise svg.bg { position: absolute; inset: 0; }
  .promise-text { position: absolute; left: 84px; top: 22px; font-size: 24px; line-height: 30px; color: var(--white); }
  .promise-text .pink { color: var(--pink); }
  .promise .heart { position: absolute; left: 38px; top: 22px; }

  .tagline { position: absolute; left: 40px; top: 848px; width: 580px; font-family: 'Montserrat', sans-serif; font-weight: 700; font-size: 15px; letter-spacing: 1.5px; text-transform: uppercase; color: var(--pink); }

  .features { position: absolute; left: 40px; top: 884px; display: flex; }
  .feature { width: 144px; display: flex; flex-direction: column; align-items: center; text-align: center; font-family: 'Montserrat', sans-serif; font-weight: 600; font-size: 13px; line-height: 17px; color: var(--ink); position: relative; }
  .feature + .feature::before { content: ""; position: absolute; left: 0; top: 30px; height: 80px; border-left: 1px solid var(--pink-soft); }
  .feature svg { margin-bottom: 12px; }

  .band { position: absolute; left: 0; top: 1040px; width: 960px; height: 160px; }
  .band-heart { position: absolute; left: 72px; top: 1074px; }
  .band-text { position: absolute; left: 177px; top: 1098px; font-size: 25px; line-height: 31px; color: var(--white); }
  .band-text .pink { color: var(--pink); }

  .note { position: absolute; left: 662px; top: 900px; width: 290px; height: 262px; transform: rotate(1deg); }
  .note-text { position: absolute; left: 44px; top: 58px; width: 220px; text-align: center; font-family: 'Caveat', cursive; font-weight: 500; font-size: 36px; line-height: 36px; color: var(--plum); }
  .note-text .pink { color: var(--pink); font-size: 44px; display: inline-block; margin-top: 6px; }
</style>
</head>
<body>
<main class="poster">
  <div class="photo" role="img" aria-label="Photo of two smiling women sharing a warm hug in a bright store aisle"></div>

  <div class="logo">
    <svg width="270" height="96" viewBox="0 0 270 96"><path d="M6 8 L262 4 L266 20 L258 46 L268 70 L260 92 L12 90 L2 74 L8 50 L0 28 Z" fill="var(--plum)"/></svg>
    <span class="logo-name">QUILVO</span>
    <span class="logo-tag">RT IN YOUR POCKET</span>
  </div>

  <svg class="heart-top" width="52" height="76" viewBox="0 0 52 76"><path d="M14 72 C10 56 2 40 4 22 C6 8 20 6 24 22 C30 4 48 4 46 18 C44 34 24 48 14 72" fill="none" stroke="var(--pink)" stroke-width="2.4" stroke-linecap="round"/></svg>

  <h1 class="headline">Eat<br>the food<br><span class="pink">you love.</span></h1>
  <svg class="rule-1" width="240" height="14" viewBox="0 0 240 14"><path d="M2 10 Q120 2 238 4" stroke="var(--pink)" stroke-width="3.5" fill="none" stroke-linecap="round"/></svg>

  <h2 class="subhead">Stay<br>accountable</h2>
  <div class="script">every day.</div>
  <svg class="rule-2" width="260" height="12" viewBox="0 0 260 12"><path d="M2 6 Q130 2 258 7" stroke="var(--pink)" stroke-width="3" fill="none" stroke-linecap="round"/></svg>

  <div class="promise">
    <svg class="bg" width="390" height="134" viewBox="0 0 390 134"><path d="M10 6 L370 2 L384 30 L376 62 L390 96 L378 130 L14 132 L2 106 L8 68 L0 32 Z" fill="var(--plum)"/></svg>
    <svg class="heart" width="34" height="30" viewBox="0 0 34 30"><path d="M17 27 C6 19 2 13 2 8 C2 3 7 1 11 2 C14 3 16 5 17 8 C18 5 20 3 23 2 C27 1 32 3 32 8 C32 13 28 19 17 27 Z" fill="none" stroke="var(--pink)" stroke-width="2.2"/></svg>
    <p class="promise-text">Real support.<br>Real connection.<br><span class="pink">Real results.</span></p>
  </div>

  <p class="tagline">Stay Consistent with RT in Your Pocket!</p>

  <section class="features">
    <div class="feature">
      <svg width="76" height="76" viewBox="0 0 76 76"><circle cx="38" cy="38" r="36" fill="none" stroke="var(--pink)" stroke-width="1.5"/><path d="M22 38 H54 C54 48 47 54 38 54 C29 54 22 48 22 38 Z" fill="var(--pink)"/><path d="M38 30 C33 26 33 22 36 21 C37.5 21 38 22 38 23 C38 22 38.5 21 40 21 C43 22 43 26 38 30 Z" fill="none" stroke="var(--pink)" stroke-width="1.6"/></svg>
      Enjoy your<br>favorite foods
    </div>
    <div class="feature">
      <svg width="76" height="76" viewBox="0 0 76 76"><circle cx="38" cy="38" r="36" fill="none" stroke="var(--pink)" stroke-width="1.5"/><rect x="26" y="18" width="20" height="38" rx="3" fill="none" stroke="var(--pink)" stroke-width="2.2"/><circle cx="36" cy="51" r="1.6" fill="var(--pink)"/><circle cx="48" cy="34" r="9" fill="var(--pink)"/><path d="M48 38 C45 36 44 34 45 33 C46 32 47.5 32 48 33.5 C48.5 32 50 32 51 33 C52 34 51 36 48 38 Z" fill="var(--white)"/></svg>
      Daily check-ins<br>from RT
    </div>
    <div class="feature">
      <svg width="76" height="76" viewBox="0 0 76 76"><circle cx="38" cy="38" r="36" fill="none" stroke="var(--pink)" stroke-width="1.5"/><circle cx="38" cy="30" r="5" fill="var(--pink)"/><circle cx="26" cy="33" r="4" fill="var(--pink)"/><circle cx="50" cy="33" r="4" fill="var(--pink)"/><path d="M30 48 C30 40 46 40 46 48 Z M19 48 C19 42 29 41 29 45 L29 48 Z M57 48 C57 42 47 41 47 45 L47 48 Z" fill="var(--pink)"/></svg>
      Encouragement<br>that keeps you<br>going
    </div>
    <div class="feature">
      <svg width="76" height="76" viewBox="0 0 76 76"><circle cx="38" cy="38" r="36" fill="none" stroke="var(--pink)" stroke-width="1.5"/><path d="M22 54 L32 30 L46 44 Z" fill="none" stroke="var(--pink)" stroke-width="2.2" stroke-linejoin="round"/><path d="M40 28 L44 22 M48 32 L54 28 M46 24 L50 18" stroke="var(--pink)" stroke-width="2" stroke-linecap="round"/><circle cx="52" cy="38" r="1.6" fill="var(--pink)"/><circle cx="38" cy="20" r="1.6" fill="var(--pink)"/></svg>
      Accountability<br>that fits your life
    </div>
  </section>

  <svg class="band" width="960" height="160" viewBox="0 0 960 160"><path d="M0 12 L60 6 L140 14 L240 4 L330 12 L420 6 L520 14 L620 8 L720 12 L820 4 L900 10 L960 6 L960 160 L0 160 Z" fill="var(--plum)"/></svg>
  <svg class="band-heart" width="86" height="106" viewBox="0 0 86 106"><path d="M38 100 C26 78 6 60 6 34 C6 12 30 8 40 30 C48 6 80 6 80 28 C80 56 56 74 38 100 M38 100 L46 104" fill="none" stroke="var(--pink)" stroke-width="3" stroke-linecap="round"/></svg>
  <p class="band-text"><span class="pink">RT</span> is in your pocket<br>so you can stay focused on <span class="pink">you</span>.</p>

  <div class="note">
    <svg width="290" height="262" viewBox="0 0 290 262" style="position:absolute;inset:0"><path d="M4 4 L282 8 L286 120 L290 258 L8 254 L2 130 Z" fill="var(--note)"/><rect x="70" y="-2" width="96" height="26" fill="var(--tape)" opacity="0.85" transform="rotate(-3 118 11)"/><path d="M150 238 C138 224 124 210 130 198 C136 188 148 194 150 204 C154 192 170 188 174 198 C178 210 160 222 150 238" fill="none" stroke="var(--pink)" stroke-width="2.4" stroke-linecap="round"/></svg>
    <p class="note-text">You don't<br>have to do this<br><span class="pink">alone.</span></p>
  </div>
</main>
</body>
</html>
```